Corvex Hiring Partners Business Cards

Business cards with logo design for a new recruiting company called "Corvex Hiring Partners"

incorporate RED & BLUE colors

Final design should reflect strength - clean, elegant design

Company name superimposed upon graphic (Greek Columns)

Please see attached Photos!!!

Industry/Entity Type

Business

Font styles to use
Decorative

Colors
ec2027
0555a3
85cae6

Requirements
Must have
• Must look very similar to attached design!!!

Want Company name superimposed upon graphic (Greek Columns)

Tag line at bottom must be included:
"Building Outstanding Companies through Outstanding People"

```html
<!DOCTYPE html>
<html lang="en">
<head>
<meta charset="utf-8">
<title>Corvex Hiring Partners – Business Card</title>
<link rel="stylesheet" href="https://fonts.googleapis.com/css2?family=Marcellus&display=swap">
<style>
  :root {
    --brand-red: #ec2027;
    --brand-blue: #0555a3;
    --brand-sky: #85cae6;
    --card-white: #ffffff;
    --backdrop: #e8e9eb;
    --type: "Marcellus", serif;
  }
  * { margin: 0; padding: 0; box-sizing: border-box; }
  html, body {
    width: 1200px;
    height: 845px;
    overflow: hidden;
    background: var(--backdrop);
    font-family: var(--type);
  }
  .business-card {
    position: absolute;
    left: 70px;
    top: 120px;
    width: 1060px;
    height: 606px;
    border-radius: 40px;
    background: var(--card-white);
    overflow: hidden;
    box-shadow: 0 10px 30px rgba(0,0,0,0.15);
  }
  .card-waves {
    position: absolute;
    inset: 0;
    width: 100%;
    height: 100%;
  }
  .wave-red { fill: var(--brand-red); }
  .wave-blue { fill: var(--brand-blue); }
  .wave-line { fill: none; stroke: var(--card-white); stroke-width: 5; }

  .brand {
    position: absolute;
    left: 70px;
    top: 120px;
    display: flex;
    align-items: flex-start;
    gap: 22px;
  }
  .brand-mark {
    width: 26px;
    height: 26px;
    border-radius: 50%;
    background: var(--brand-blue);
    margin-top: 14px;
  }
  .brand-name {
    font-family: var(--type);
    font-weight: 400;
    color: var(--brand-blue);
    font-size: 50px;
    line-height: 1.1;
    letter-spacing: 1px;
  }

  .holder-name {
    position: absolute;
    right: 70px;
    top: 74px;
    font-family: var(--type);
    font-weight: 400;
    font-size: 42px;
    color: var(--brand-blue);
  }

  .contact-list {
    position: absolute;
    right: 70px;
    top: 318px;
    list-style: none;
    color: var(--card-white);
    font-size: 25px;
    text-align: right;
  }
  .contact-list li {
    display: flex;
    align-items: center;
    justify-content: flex-end;
    gap: 12px;
    margin-bottom: 12px;
  }
  .contact-icon { width: 26px; height: 26px; flex: none; }
  .contact-icon * { fill: none; stroke: var(--card-white); stroke-width: 2; }
  .contact-icon .solid { fill: var(--card-white); stroke: none; }

  .tagline {
    position: absolute;
    right: 60px;
    top: 478px;
    color: var(--card-white);
    font-size: 32px;
    line-height: 1.3;
    text-align: right;
  }
</style>
</head>
<body>
  <article class="business-card">
    <svg class="card-waves" viewBox="0 0 1060 606" preserveAspectRatio="none" aria-hidden="true">
      <path class="wave-red" d="M0,410 C250,470 380,460 560,310 C720,190 900,165 1060,160 L1060,212 C900,216 760,230 640,330 C440,500 260,495 0,440 Z"/>
      <path class="wave-blue" d="M0,460 C260,525 420,520 600,360 C740,250 900,240 1060,238 L1060,606 L0,606 Z"/>
      <path class="wave-line" d="M0,530 C180,575 300,580 400,560"/>
    </svg>

    <div class="brand">
      <span class="brand-mark"></span>
      <div class="brand-name">Corvex<br>Hiring<br>Partners</div>
    </div>

    <h1 class="holder-name">Daniel R. Whitmore</h1>

    <ul class="contact-list">
      <li>
        <svg class="contact-icon" viewBox="0 0 26 26" aria-hidden="true">
          <circle cx="13" cy="13" r="11"/>
          <path class="solid" d="M9,7 L11,7 L12,10 L10.5,11.5 C11.5,13.5 12.5,14.5 14.5,15.5 L16,14 L19,15 L19,17 C19,18 18,19 17,19 C12,19 7,14 7,9 C7,8 8,7 9,7 Z"/>
        </svg>
        <span>512-555-0142</span>
      </li>
      <li>
        <svg class="contact-icon" viewBox="0 0 26 26" aria-hidden="true">
          <rect x="3" y="6" width="20" height="14" rx="1"/>
          <path d="M3,7 L13,14 L23,7"/>
        </svg>
        <span>DWhitmore@CorvexHP.com</span>
      </li>
      <li>
        <svg class="contact-icon" viewBox="0 0 26 26" aria-hidden="true">
          <circle cx="13" cy="13" r="10"/>
          <ellipse cx="13" cy="13" rx="4.5" ry="10"/>
          <path d="M3,13 L23,13 M5,8 L21,8 M5,18 L21,18"/>
        </svg>
        <span>www.CorvexHP.com</span>
      </li>
    </ul>

    <p class="tagline">Building Outstanding Companies<br>through Outstanding People</p>
  </article>
</body>
</html>
```